New business card/stationary for a consulting company

I am looking for a clean and very professional looking business card for my consulting company as well as corresponding stationary. I am uploading our logo. I like simple and powerful for the feel. No graphics but I am open on everything else. Below is my contact information but would like the final to be in a version I can add my employees information into and print. Thank you.

Daniel Whitcombe
dan@ferncliffadvisory.com
2870 North 9th Avenue, Summit Floor, Elm Ridge, Illinois 60531
www.ferncliffadvisory.com

Industry/Entity Type

Consulting

Contact Information for Business Card

Daniel Whitcombe
dan@ferncliffadvisory.com
www.ferncliffadvisory.com

Font styles to use
Serif
Sans Serif

Requirements
Must have
• Our logo and the business card details.
Nice to have
• our website www.ferncliffadvisory.com

```html
<!DOCTYPE html>
<html lang="en">
<head>
<meta charset="utf-8">
<title>Ferncliff Advisory — Business Card</title>
<link href="https://fonts.googleapis.com/css2?family=Questrial&family=PT+Sans&display=swap" rel="stylesheet">
<style>
  :root {
    --backdrop: #3b3431;
    --card-white: #f4f4f4;
    --navy: #1c1a6b;
    --navy-deep: #201d63;
    --silver: #c9c9cc;
    --rule: #9a9a9a;
    --ink: #2b2b2b;
  }
  * { box-sizing: border-box; margin: 0; padding: 0; }
  html, body {
    width: 1200px; height: 900px; overflow: hidden;
    background: var(--backdrop);
  }
  .stage {
    width: 1200px; height: 900px;
    display: flex; align-items: center; justify-content: center; gap: 40px;
  }
  .card {
    position: relative;
    width: 540px; height: 309px;
    box-shadow: 0 10px 28px rgba(0,0,0,.45);
  }
  .card--front { background: var(--card-white); }
  .card--back { background: var(--navy-deep); }

  /* Front */
  .brand-block {
    position: absolute; left: 44px; top: 50px;
    display: flex; align-items: center; gap: 12px;
    font-family: "Questrial", sans-serif;
    color: var(--navy);
  }
  .brand-square { width: 26px; height: 26px; background: var(--navy); }
  .brand-name { font-size: 25px; letter-spacing: 1.5px; text-transform: uppercase; }
  .header-rule {
    position: absolute; left: 44px; right: 30px; top: 108px;
    height: 1px; background: var(--rule);
  }
  .address {
    position: absolute; right: 30px; top: 122px;
    font-family: "PT Sans", sans-serif; font-size: 13px; line-height: 1.35;
    color: var(--ink); text-align: right;
  }
  .person-name {
    position: absolute; left: 44px; top: 188px;
    font-family: "Questrial", sans-serif; font-size: 19px; letter-spacing: 1px;
    color: var(--navy); text-transform: uppercase;
  }
  .contact-list {
    position: absolute; left: 44px; top: 230px;
    list-style: none;
    font-family: "PT Sans", sans-serif; font-size: 14px; color: var(--ink);
  }
  .contact-list li { display: flex; align-items: center; gap: 8px; line-height: 1.6; }
  .contact-icon { width: 12px; height: 12px; flex: none; }

  /* Back */
  .back-brand {
    position: absolute; inset: 0;
    display: flex; flex-direction: column; align-items: center; justify-content: center; gap: 18px;
    font-family: "Questrial", sans-serif; color: var(--silver);
  }
  .back-square { width: 30px; height: 30px; background: var(--silver); }
  .back-name { font-size: 30px; letter-spacing: 2px; text-transform: uppercase; }
</style>
</head>
<body>
<main class="stage">
  <section class="card card--front" aria-label="Business card front">
    <div class="brand-block">
      <span class="brand-square"></span>
      <span class="brand-name">Ferncliff Advisory</span>
    </div>
    <div class="header-rule"></div>
    <address class="address">
      2870 North 9th Avenue,<br>
      Summit Floor, Elm Ridge,<br>
      Illinois 60531
    </address>
    <h1 class="person-name">Daniel Whitcombe</h1>
    <ul class="contact-list">
      <li>
        <svg class="contact-icon" viewBox="0 0 12 12" aria-hidden="true">
          <rect x="0.5" y="2" width="11" height="8" fill="var(--navy)"/>
          <path d="M0.5 2 L6 6.5 L11.5 2" fill="none" stroke="#fff" stroke-width="1"/>
        </svg>
        dan@ferncliffadvisory.com
      </li>
      <li>
        <svg class="contact-icon" viewBox="0 0 12 12" aria-hidden="true">
          <circle cx="6" cy="6" r="5.5" fill="var(--navy)"/>
          <path d="M1 6 H11 M6 0.5 C3.5 3 3.5 9 6 11.5 M6 0.5 C8.5 3 8.5 9 6 11.5" fill="none" stroke="#fff" stroke-width="0.8"/>
        </svg>
        www.ferncliffadvisory.com
      </li>
    </ul>
  </section>

  <section class="card card--back" aria-label="Business card back">
    <div class="back-brand">
      <span class="back-square"></span>
      <span class="back-name">Ferncliff Advisory</span>
    </div>
  </section>
</main>
</body>
</html>
```